Halvex Power

We need a business card for "Halvex power". I have uploaded the logo, the color of the card should be according to the logo "Blackish".
Basically halvex power is a solar company.
Also we would like a sample file in which we can edit the information such names and contact details ourselves
The card would be two sided with following details
1- logo on front and underneath the logo there should be a line saying
"Cleaner . Cheaper . Power"
2-website i.e "www.halvexpowerco.com"
3- Icons for Facebook and Instagram that tells the clients we are available on both social sites.
4- name of the person with his/her designation underneath and email address
5-contact number
6- 1-800--- number with the extension number

its up to the designer how he/she places the details,but it must look professional

Industry/Entity Type

Business

Contact Information for Business Card

5-contact number

Requirements
Must have
• 1- logo on front and underneath the logo there should be a line saying
• "Cleaner . Cheaper . Power"
• 2-website i.e "www.halvexpowerco.com"
• 3- Icons for Facebook and Instagram that tells the clients we are available on both social sites.
• 4- name of the person with his/her designation underneath and email address
• 5-contact number of the person
• 6- 1-800--- number with the extension number
• 7-card should be in black shade like the logo

```html
<!DOCTYPE html>
<html lang="en">
<head>
<meta charset="utf-8">
<title>Halvex Power – Business Card</title>
<link rel="stylesheet" href="https://fonts.googleapis.com/css2?family=Arimo:wght@400;700&display=swap">
<style>
  :root {
    --page-bg: #ece7df;
    --card-light: #ffffff;
    --card-dark: #4a4a4a;
    --brand-green: #7dc242;
    --ink: #3a3a3a;
    --rule: #6a6a6a;
    --social: #3b5b98;
  }
  * { box-sizing: border-box; margin: 0; padding: 0; }
  html, body { width: 1200px; height: 900px; overflow: hidden; }
  body {
    position: relative;
    background: var(--page-bg);
    font-family: "Arimo", Arial, sans-serif;
    color: var(--ink);
  }
  .card {
    position: absolute;
    top: 275px;
    width: 478px;
    height: 295px;
    box-shadow: 0 3px 6px rgba(0,0,0,0.25);
  }
  .card-front {
    left: 116px;
    background: var(--card-light);
    border-radius: 0 46px 0 46px;
  }
  .card-back {
    left: 622px;
    background: var(--card-dark);
    border-radius: 46px 0 46px 0;
  }

  .brand-name {
    position: absolute;
    font-weight: 700;
    color: var(--brand-green);
    white-space: nowrap;
    letter-spacing: -0.5px;
  }
  .card-front .brand-name {
    right: 28px;
    top: 50px;
    font-size: 34px;
    line-height: 40px;
  }
  .tagline {
    position: absolute;
    right: 28px;
    top: 94px;
    font-size: 11px;
    letter-spacing: 2.4px;
    color: var(--ink);
    white-space: nowrap;
  }
  .card-back .brand-name {
    left: 0;
    right: 0;
    top: 124px;
    text-align: center;
    font-size: 46px;
  }

  .person {
    position: absolute;
    left: 26px;
    top: 167px;
  }
  .person-name {
    font-size: 17px;
    font-weight: 700;
    color: var(--ink);
    letter-spacing: 0.2px;
  }
  .person-name .first { color: var(--brand-green); }
  .person-role {
    font-size: 13px;
    color: var(--ink);
    margin-top: 2px;
  }
  .role-rule {
    position: absolute;
    left: 149px;
    top: 195px;
    width: 250px;
    height: 1px;
    background: var(--rule);
  }
  .social {
    position: absolute;
    top: 185px;
    right: 27px;
    display: flex;
    gap: 7px;
  }
  .social-box {
    width: 19px;
    height: 19px;
    background: var(--social);
  }

  .phones {
    position: absolute;
    left: 26px;
    top: 226px;
    font-size: 13.5px;
    line-height: 17px;
    color: var(--ink);
  }
  .phones li, .links li {
    list-style: none;
    display: flex;
    align-items: center;
    gap: 6px;
    white-space: nowrap;
  }
  .links {
    position: absolute;
    right: 27px;
    top: 228px;
    font-size: 13.5px;
    line-height: 18px;
    color: var(--ink);
    text-align: right;
  }
  .links li { justify-content: flex-end; }
  .icon { width: 10px; height: 10px; flex: none; }
</style>
</head>
<body>

<section class="card card-front" aria-label="Business card front">
  <div class="brand-name">Halvex Power</div>
  <div class="tagline">Cleaner . Cheaper . Power</div>

  <div class="person">
    <div class="person-name"><span class="first">MARCUS</span> ELLERY</div>
    <div class="person-role">Managing Director</div>
  </div>
  <div class="role-rule"></div>
  <div class="social" aria-label="Social profiles">
    <span class="social-box"></span>
    <span class="social-box"></span>
  </div>

  <ul class="phones">
    <li>
      <svg class="icon" viewBox="0 0 10 10" aria-hidden="true"><rect x="2.5" y="0.5" width="5" height="9" rx="1" fill="none" stroke="#7dc242" stroke-width="1.2"/></svg>
      044-555 018 274
    </li>
    <li>
      <svg class="icon" viewBox="0 0 10 10" aria-hidden="true"><path d="M1 4 Q5 0 9 4 L8 5 L6.5 4 L3.5 4 L2 5 Z" fill="#7dc242"/><rect x="2" y="5.5" width="6" height="3.5" rx="0.6" fill="#7dc242"/></svg>
      1-800-555-0142 ext. 21
    </li>
  </ul>

  <ul class="links">
    <li>info@halvexpowerco.com
      <svg class="icon" viewBox="0 0 10 10" aria-hidden="true"><rect x="0.5" y="2" width="9" height="6" fill="#7dc242"/><path d="M0.5 2 L5 5.5 L9.5 2" fill="none" stroke="#fff" stroke-width="0.9"/></svg>
    </li>
    <li>www.halvexpowerco.com
      <svg class="icon" viewBox="0 0 10 10" aria-hidden="true"><circle cx="5" cy="5" r="4.5" fill="#7dc242"/><path d="M0.5 5 H9.5 M5 0.5 V9.5" stroke="#fff" stroke-width="0.7"/></svg>
    </li>
  </ul>
</section>

<section class="card card-back" aria-label="Business card back">
  <div class="brand-name">Halvex Power</div>
</section>

</body>
</html>
```